MES Modul-Struktur grafisch veranschaulichen
Zielgruppe
Wir sind Software-Hersteller. Thema 'MES'. Unsere Kunden sind Produktionsunternehmen.
Mit einem MES (Manufacturing Execution System) werden Produktionsprozesse überwacht, geplant, gesteuert und optimiert. Allgemein geht es darum, die Produktivität zu steigern und Kosten zu minimieren.
Eine MES-Software ist modular strukturiert, so dass der Kunde sich nach Bedarf die einzelnen Funktionsmodule zusammenstellen kann. Unser MES KORVIN 7 MAX besteht z.B. aus folgenden Einzelmodulen:
- BASIS (Basismodul)
- MDE (Maschinendatenerfassung)
- BDE (Betriebsdatenerfassung)
- INST (Instandhaltung)
- ALARM (Alarmierung)
- DOK (Dokumentenmanagement)
- TNT (Traceability)
- PLAN (Feinplanung/Leitstand)
- LOG (Logistik)
- VIS (Visualisierung)
- PEP (Personaleinsatzplanung)
- MPZE (Personalzeiterfassung)
- DNC (Rezepturen/DNC)
- EM (Energiemonitoring)
Aufgabenstellung
Die modulare Struktur und der große Umfang an Modulen ist ein wichtiger Vorteil für unsere Kunden, da Sie nicht so schnell an Grenzen stoßen und sich dann unter Umständen eine weitere Insellösung (extra Software mit extra Datenbank ...) anschaffen müssen.
Wichtig ist, dass die einzelnen Module funktionell ineinandergreifen und alle auf die gleiche Datenbank zugreifen.
Es reicht wenn in der Grafik die Module nur mit er Abkürzung, also z.B. MDE bezeichnet werden. Für den ersten Entwurf können auch Platzhalter genutzt werden.
Der Betrachter sollte aus der Grafik auf den ersten Blick erkennen:
- umfängliches MES
- modular strukturiert
- Funktionsmodule step-by-step erweiterbar
Für die Umsetzung naheliegend wären Puzzle-Steine, Blokkis, ... muss aber nicht.

```html
<!DOCTYPE html>
<html lang="de">
<head>
<meta charset="utf-8">
<title>MES-Struktur</title>
<link href="https://fonts.googleapis.com/css2?family=Open+Sans:wght@400;600;700&display=swap" rel="stylesheet">
<style>
  :root{
    --bg:#e3e7ea;
    --ink:#3b3b3b;
    --ring:#cbd4db;
    --basis:#c4ccd3;
    --mde:#f6b400;
    --bde:#ee8800;
    --inst:#e6501d;
    --alarm:#b6cb22;
    --dok:#5eab2f;
    --tnt:#17a03d;
    --plan:#0b7b3b;
    --log:#0a5b2b;
    --vis:#3f2a6c;
    --pep:#6f3a78;
    --mpze:#1d5a9d;
    --dnc:#2d8ecb;
    --em:#7ec4e8;
  }
  *{margin:0;padding:0;box-sizing:border-box}
  html,body{width:848px;height:1200px;overflow:hidden}
  body{background:var(--bg);font-family:"Open Sans",Arial,sans-serif;color:var(--ink);position:relative}
  .title{position:absolute;top:34px;left:0;width:848px;text-align:center;font-size:32px;font-weight:700;letter-spacing:-.3px}
  .module-wheel{position:absolute;left:0;top:80px;width:848px;height:760px}
  .piece-label{fill:#fff;font-family:"Open Sans",Arial,sans-serif;font-weight:600;font-size:22px;text-anchor:middle;dominant-baseline:central}
  .basis-label{fill:#fff;font-family:"Open Sans",Arial,sans-serif;font-weight:600;font-size:21px;text-anchor:middle}
  .icon{fill:none;stroke:#fff;stroke-width:3;stroke-linecap:round;stroke-linejoin:round}
  .icon .solid{fill:#fff;stroke:none}
  .legend{position:absolute;left:31px;top:923px;width:785px;height:248px;background:#fff;border-radius:10px;box-shadow:0 -2px 0 #d3d9de;padding:22px 0 0 0}
  .legend-col{position:absolute;top:20px;list-style:none}
  .legend-col.left{left:20px}
  .legend-col.right{left:403px}
  .legend-item{display:flex;align-items:center;height:31.3px;font-size:19px}
  .legend-dot{width:12px;height:12px;border-radius:50%;margin-right:8px;flex:none}
  .legend-abbr{font-weight:700;width:84px;flex:none}
  .legend-name{font-weight:400}
</style>
</head>
<body>
  <h1 class="title">MES-Struktur</h1>

  <svg class="module-wheel" viewBox="-424 -373 848 760" aria-label="Modulare MES-Struktur als Puzzle-Kreis">
    <defs>
      <path id="wedge" d="M108.7,-26.8 L344.7,-85 A355,355 0 0 1 344.7,85 L108.7,26.8 A112,112 0 0 0 108.7,-26.8 Z"/>
      <path id="knob" d="M208.7,51.5 A17,17 0 1 0 237.9,58.7"/>
    </defs>

    <circle class="outer-ring" r="373" fill="var(--ring)"/>
    <circle r="359" fill="#fff"/>

    <!-- wedges -->
    <g stroke="#fff" stroke-width="4" stroke-linejoin="round">
      <use href="#wedge" transform="rotate(-110)" fill="var(--mde)"/>
      <use href="#wedge" transform="rotate(-82.3)" fill="var(--bde)"/>
      <use href="#wedge" transform="rotate(-54.6)" fill="var(--inst)"/>
      <use href="#wedge" transform="rotate(-26.9)" fill="var(--alarm)"/>
      <use href="#wedge" transform="rotate(0.8)" fill="var(--dok)"/>
      <use href="#wedge" transform="rotate(28.5)" fill="var(--tnt)"/>
      <use href="#wedge" transform="rotate(56.1)" fill="var(--plan)"/>
      <use href="#wedge" transform="rotate(83.8)" fill="var(--log)"/>
      <use href="#wedge" transform="rotate(111.5)" fill="var(--vis)"/>
      <use href="#wedge" transform="rotate(139.2)" fill="var(--pep)"/>
      <use href="#wedge" transform="rotate(166.9)" fill="var(--mpze)"/>
      <use href="#wedge" transform="rotate(194.6)" fill="var(--dnc)"/>
      <use href="#wedge" transform="rotate(222.3)" fill="var(--em)"/>
    </g>

    <!-- puzzle knobs -->
    <g stroke="#fff" stroke-width="4">
      <use href="#knob" transform="rotate(-110)" fill="var(--mde)"/>
      <use href="#knob" transform="rotate(-82.3) translate(50,12)" fill="var(--bde)"/>
      <use href="#knob" transform="rotate(-54.6)" fill="var(--inst)"/>
      <use href="#knob" transform="rotate(-26.9) translate(50,12)" fill="var(--alarm)"/>
      <use href="#knob" transform="rotate(0.8)" fill="var(--dok)"/>
      <use href="#knob" transform="rotate(28.5) translate(50,12)" fill="var(--tnt)"/>
      <use href="#knob" transform="rotate(56.1)" fill="var(--plan)"/>
      <use href="#knob" transform="rotate(83.8) translate(50,12)" fill="var(--log)"/>
      <use href="#knob" transform="rotate(111.5)" fill="var(--vis)"/>
      <use href="#knob" transform="rotate(139.2) translate(50,12)" fill="var(--pep)"/>
      <use href="#knob" transform="rotate(166.9)" fill="var(--mpze)"/>
      <use href="#knob" transform="rotate(194.6) translate(50,12)" fill="var(--dnc)"/>
      <use href="#knob" transform="rotate(222.3) translate(-40,-10)" fill="var(--em)"/>
    </g>

    <!-- labels -->
    <g>
      <text class="piece-label" transform="rotate(-110) translate(300,0) rotate(110)">MDE</text>
      <text class="piece-label" transform="rotate(-82.3) translate(300,0) rotate(82.3)">BDE</text>
      <text class="piece-label" transform="rotate(-54.6) translate(300,0) rotate(54.6)">INST</text>
      <text class="piece-label" transform="rotate(-26.9) translate(300,0) rotate(26.9)">ALARM</text>
      <text class="piece-label" transform="rotate(0.8) translate(305,0) rotate(-0.8)">DOK</text>
      <text class="piece-label" transform="rotate(28.5) translate(305,0) rotate(-28.5)">TNT</text>
      <text class="piece-label" transform="rotate(56.1) translate(300,0) rotate(-56.1)">PLAN</text>
      <text class="piece-label" transform="rotate(83.8) translate(300,0) rotate(-83.8)">LOG</text>
      <text class="piece-label" transform="rotate(111.5) translate(300,0) rotate(-111.5)">VIS</text>
      <text class="piece-label" transform="rotate(139.2) translate(300,0) rotate(-139.2)">PEP</text>
      <text class="piece-label" transform="rotate(166.9) translate(300,0) rotate(-166.9)">MPZE</text>
      <text class="piece-label" transform="rotate(194.6) translate(300,0) rotate(-194.6)">DNC</text>
      <text class="piece-label" transform="rotate(222.3) translate(300,0) rotate(-222.3)">EM</text>
    </g>

    <!-- icons -->
    <g class="icon">
      <!-- MDE: gears and pencil -->
      <g transform="rotate(-110) translate(185,0) rotate(110)">
        <circle cx="-8" cy="-4" r="8"/><circle cx="-8" cy="-4" r="2.5"/>
        <circle cx="4" cy="10" r="6"/>
        <path d="M8,-14 L20,-2 M6,-12 L18,0"/>
      </g>
      <!-- BDE: chart with magnifier -->
      <g transform="rotate(-82.3) translate(185,0) rotate(82.3)">
        <path d="M-18,-16 V16 H18"/>
        <path d="M-11,10 V2 M-5,10 V-6"/>
        <circle cx="6" cy="-2" r="7"/><path d="M11,3 L17,10"/>
      </g>
      <!-- INST: tools -->
      <g transform="rotate(-54.6) translate(185,0) rotate(54.6)">
        <path d="M-15,-15 L15,15 M15,-15 L-15,15" stroke-width="4.5"/>
        <circle cx="-15" cy="-15" r="4"/>
      </g>
      <!-- ALARM: signal -->
      <g transform="rotate(-26.9) translate(190,0) rotate(26.9)">
        <circle class="solid" r="5"/>
        <path d="M-10,-10 A14,14 0 0 0 -10,10 M10,-10 A14,14 0 0 1 10,10"/>
        <path d="M-16,-16 A22,22 0 0 0 -16,16 M16,-16 A22,22 0 0 1 16,16"/>
      </g>
      <!-- DOK: document -->
      <g transform="rotate(0.8) translate(190,0) rotate(-0.8)">
        <path d="M-12,-17 H6 L13,-10 V17 H-12 Z"/>
        <path d="M-6,-4 H7 M-6,3 H7 M-6,10 H7"/>
      </g>
      <!-- TNT: shuffle -->
      <g transform="rotate(28.5) translate(190,0) rotate(-28.5)">
        <path d="M-16,-8 H-6 L6,8 H15 M-16,8 H-6 L6,-8 H15"/>
        <path d="M10,-13 L15,-8 L10,-3 M10,3 L15,8 L10,13"/>
      </g>
      <!-- PLAN: calendar -->
      <g transform="rotate(56.1) translate(190,0) rotate(-56.1)">
        <rect x="-16" y="-13" width="32" height="29" rx="3"/>
        <path d="M-16,-5 H16 M-8,-18 V-9 M8,-18 V-9"/>
        <path d="M-9,3 H-5 M-1,3 H3 M7,3 H10 M-9,10 H-5 M-1,10 H3 M7,10 H10"/>
      </g>
      <!-- LOG: truck -->
      <g transform="rotate(83.8) translate(190,0) rotate(-83.8)">
        <rect x="-20" y="-12" width="24" height="18" rx="1"/>
        <path d="M4,-6 H12 L18,2 V6 H4"/>
        <circle cx="-12" cy="10" r="4"/><circle cx="11" cy="10" r="4"/>
      </g>
      <!-- VIS: eye -->
      <g transform="rotate(111.5) translate(190,0) rotate(-111.5)">
        <path d="M-20,0 Q0,-18 20,0 Q0,18 -20,0 Z"/>
        <circle class="solid" r="6"/>
      </g>
      <!-- PEP: team -->
      <g transform="rotate(139.2) translate(190,0) rotate(-139.2)">
        <circle class="solid" cx="0" cy="-12" r="5"/>
        <circle class="solid" cx="-13" cy="-8" r="4"/>
        <circle class="solid" cx="13" cy="-8" r="4"/>
        <rect class="solid" x="-5" y="-5" width="10" height="20" rx="3"/>
        <rect class="solid" x="-17" y="-2" width="8" height="15" rx="3"/>
        <rect class="solid" x="9" y="-2" width="8" height="15" rx="3"/>
      </g>
      <!-- MPZE: clock -->
      <g transform="rotate(166.9) translate(190,0) rotate(-166.9)">
        <circle r="16"/><path d="M0,-9 V0 L7,5"/>
      </g>
      <!-- DNC: network -->
      <g transform="rotate(194.6) translate(190,0) rotate(-194.6)">
        <rect class="solid" x="-5" y="-17" width="10" height="8"/>
        <rect class="solid" x="-19" y="9" width="9" height="8"/>
        <rect class="solid" x="-4.5" y="9" width="9" height="8"/>
        <rect class="solid" x="10" y="9" width="9" height="8"/>
        <path d="M0,-9 V9 M-14.5,9 V2 H14.5 V9" stroke-width="2.5"/>
      </g>
      <!-- EM: battery -->
      <g transform="rotate(222.3) translate(190,0) rotate(-222.3)">
        <rect x="-19" y="-10" width="34" height="20" rx="2"/>
        <rect class="solid" x="15" y="-4" width="4" height="8"/>
        <rect class="solid" x="-15" y="-6" width="18" height="12"/>
      </g>
    </g>

    <!-- basis module -->
    <circle r="116" fill="#fff"/>
    <circle r="108" fill="var(--basis)"/>
    <text class="basis-label" y="-28">BASIS</text>
    <g transform="translate(0,12)">
      <path d="M0,22 C-4,14 -13,5 -13,-5 A13,13 0 0 1 13,-5 C13,5 4,14 0,22 Z" fill="#fff"/>
      <circle cy="-5" r="5" fill="var(--basis)"/>
    </g>
  </svg>

  <section class="legend">
    <ul class="legend-col left">
      <li class="legend-item"><span class="legend-dot" style="background:var(--basis)"></span><span class="legend-abbr">BASIS</span><span class="legend-name">Basismodul</span></li>
      <li class="legend-item"><span class="legend-dot" style="background:var(--mde)"></span><span class="legend-abbr">MDE</span><span class="legend-name">Maschinendatenerfassung</span></li>
      <li class="legend-item"><span class="legend-dot" style="background:var(--bde)"></span><span class="legend-abbr">BDE</span><span class="legend-name">Betriebsdatenerfassung</span></li>
      <li class="legend-item"><span class="legend-dot" style="background:var(--inst)"></span><span class="legend-abbr">INST</span><span class="legend-name">Instandhaltung</span></li>
      <li class="legend-item"><span class="legend-dot" style="background:var(--alarm)"></span><span class="legend-abbr">ALARM</span><span class="legend-name">Alarmierung</span></li>
      <li class="legend-item"><span class="legend-dot" style="background:var(--dok)"></span><span class="legend-abbr">DOK</span><span class="legend-name">Dokumentenmanagement</span></li>
      <li class="legend-item"><span class="legend-dot" style="background:var(--tnt)"></span><span class="legend-abbr">TNT</span><span class="legend-name">Traceability</span></li>
    </ul>
    <ul class="legend-col right">
      <li class="legend-item"><span class="legend-dot" style="background:var(--plan)"></span><span class="legend-abbr">PLAN</span><span class="legend-name">Feinplanung/Leitstand</span></li>
      <li class="legend-item"><span class="legend-dot" style="background:var(--log)"></span><span class="legend-abbr">LOG</span><span class="legend-name">Logistik</span></li>
      <li class="legend-item"><span class="legend-dot" style="background:var(--em)"></span><span class="legend-abbr">VIS</span><span class="legend-name">Visualisierung</span></li>
      <li class="legend-item"><span class="legend-dot" style="background:var(--dnc)"></span><span class="legend-abbr">PEP</span><span class="legend-name">Personaleinsatzplanung</span></li>
      <li class="legend-item"><span class="legend-dot" style="background:var(--mpze)"></span><span class="legend-abbr">MPZE</span><span class="legend-name">Personalzeiterfassung</span></li>
      <li class="legend-item"><span class="legend-dot" style="background:var(--pep)"></span><span class="legend-abbr">DNC</span><span class="legend-name">Rezepturen/DNC</span></li>
      <li class="legend-item"><span class="legend-dot" style="background:var(--vis)"></span><span class="legend-abbr">EM</span><span class="legend-name">Energiemonitoring</span></li>
    </ul>
  </section>
</body>
</html>
```